Lev Marchetti - Senior Living Audio CDs - CD Design and Cover Design

I am an executive director in an assisted living facility. I have just started speaking, training, and coaching in the Senior Living Industry. I have 4 audio files that I want to put to a CD. The names of the CD's are:

1- Leadership - Creating A Culture of Excellence in Senior Living
2- The Purpose of Your Senior Living Business
3- A Leaders Vision - Your Attention Becomes Your Intention
4- Group Interviews -A Secret in Employee Retention

I think I can use the same CD cover for each CD. I just need the same design but 4 different ones with the names above. So everything will be the same but the name change. The inside cover will be I will consider other colors but it would be great if it would look good with the logo. I also need help with designing the CD face itself. I will be using a standard Jewel CD case. I need the front cover, the inside cover, and the back. The logo will be on all three.

On the front:

Part of me thinks it should be a clean simple design with my logo, my picture, and the title. But I am also curious about the picture of me with the elderly lady. - I need the 4 designs that are the same except the title.

On the Inside:

It can be the same design but the wording will be specific to that CD and the 4 insides will be:

All businesses rise and fall with leadership. This is especially true in the senior living industry. The life of that rise or fall is based on the culture the leader creates. Learn the 3 keys to what leaders know and do. Learn what the Importance Factor is and how you can put it to work to create and sustain a winning culture that will drive your business and occupancy above the rest.

What is the purpose of your senior living business? Your understanding to the answer of this question makes all the difference. After you have gained this understanding it takes the right beliefs and behavior of associates to fulfill this purpose. What's the purpose? How is it fulfilled?

They want a captain not a boss. As a leader in senior living you steer the ship. What you put your attention on becomes the intention of your community. Your ability to create a vision, help people embrace that vision, and learn how to stay focused when the storms of the industry come raging, is the key to your success. There is a pattern to achieving this success. Come learn this pattern and how to apply it in your life and your business. It can make all the difference.

A business can not be better than it's people. The right people are the key not just people. Learn where your focus should be to hire the right people. After you hire then find out what you can do to retain them and engage them. If you want happy residents you need happy associates.

On the back it will need to have:

1- My Logo
2- www.LevMarchetti.example
3- Email: info@LevMarchetti.example
4- You could put the picture of me and the elderly lady as a watermark on the back with the above info.

I have a short turn around time and need designs quickly. I also need help with designing the CD. My picture, the logo, and the Title.

```html
<!DOCTYPE html>
<html lang="en">
<head>
<meta charset="utf-8">
<title>Lev Marchetti – Leadership CD Insert and Disc</title>
<link href="https://fonts.googleapis.com/css2?family=Lato:wght@400;700&display=swap" rel="stylesheet">
<style>
  :root{
    --page:#f3f3f1;
    --charcoal:#3a3836;
    --charcoal-deep:#2e2c2a;
    --cream:#e7dcb6;
    --cream-light:#f1ead0;
    --ink-light:#d9d6d0;
    --white:#ffffff;
    --silver:#c9c9c9;
  }
  *{box-sizing:border-box;margin:0;padding:0}
  html,body{width:1200px;height:800px;overflow:hidden;background:var(--page);font-family:"Lato",sans-serif}
  .canvas{position:relative;width:1200px;height:800px}

  /* Inside cover insert */
  .insert{position:absolute;left:50px;top:130px;width:540px;height:540px;background:var(--cream);padding:14px}
  .insert-panel{position:relative;width:100%;height:100%;background:var(--charcoal);overflow:hidden}
  .insert-title{position:absolute;left:34px;top:38px;color:var(--white);font-size:26px;font-weight:400;letter-spacing:.5px}
  .insert-copy{position:absolute;left:34px;top:92px;width:250px;color:var(--ink-light);font-size:13.5px;line-height:1.55}
  .speaker-photo{position:absolute;left:300px;top:40px;width:170px;height:430px;border-radius:60px 60px 8px 8px;background:linear-gradient(180deg,#6a6560 0%,#4a4744 35%,#3f3d3b 100%)}
  .title-badge{position:absolute;left:34px;top:370px;width:240px;height:70px;background:var(--white);border-radius:16px;display:flex;align-items:center;justify-content:center;color:var(--charcoal-deep);font-size:28px;font-weight:700;letter-spacing:1px}
  .byline{position:absolute;right:26px;bottom:18px;text-align:right;color:var(--ink-light);font-size:11px;line-height:1.4}

  /* Disc face */
  .disc{position:absolute;left:640px;top:130px;width:540px;height:540px}
  .disc-title{font-family:"Lato",sans-serif;font-size:24px;letter-spacing:4px;fill:var(--ink-light)}
  .disc-subtitle{font-family:"Lato",sans-serif;font-size:14px;letter-spacing:.5px;fill:var(--ink-light)}
  .disc-brand{font-family:"Lato",sans-serif;font-size:14px;font-weight:700;fill:var(--charcoal-deep)}
</style>
</head>
<body>
<main class="canvas">

  <section class="insert" aria-label="Inside cover">
    <div class="insert-panel">
      <h1 class="insert-title">1. Leadership</h1>
      <p class="insert-copy">All businesses rise and fall with leadership. This is especially true in the senior living industry. The life of that rise or fall is based on the culture the leader creates. Learn the 3 keys to what leaders know and do. Learn what the Importance Factor is and how you can put it to work to create and sustain a winning culture that will drive your business and occupancy above the rest.</p>
      <div class="speaker-photo" role="img" aria-label="Standing portrait of the speaker in a dark suit"></div>
      <div class="title-badge">LEADERSHIP</div>
      <p class="byline">By Executive Director<br>Lev Marchetti</p>
    </div>
  </section>

  <svg class="disc" viewBox="0 0 540 540" aria-label="Disc face">
    <defs>
      <radialGradient id="discFill" cx="50%" cy="50%" r="50%">
        <stop offset="0%" stop-color="#45423f"/>
        <stop offset="100%" stop-color="#363432"/>
      </radialGradient>
      <radialGradient id="hubFill" cx="50%" cy="50%" r="50%">
        <stop offset="40%" stop-color="#f2f2f2"/>
        <stop offset="100%" stop-color="#a9a9a9"/>
      </radialGradient>
      <path id="titleArc" d="M60,270 A210,210 0 0 1 480,270"/>
      <path id="subtitleArc" d="M90,270 A180,180 0 0 1 450,270"/>
    </defs>
    <circle cx="270" cy="270" r="268" fill="#d8d8d8"/>
    <circle cx="270" cy="270" r="262" fill="url(#discFill)"/>
    <text class="disc-title"><textPath href="#titleArc" startOffset="50%" text-anchor="middle">1. LEADERSHIP</textPath></text>
    <text class="disc-subtitle"><textPath href="#subtitleArc" startOffset="50%" text-anchor="middle">Creating A Culture Of Excellence In Senior Living</textPath></text>
    <rect x="190" y="130" width="160" height="34" rx="6" fill="var(--cream-light)"/>
    <circle cx="208" cy="147" r="7" fill="var(--charcoal-deep)"/>
    <text class="disc-brand" x="222" y="152">Lev Marchetti</text>
    <circle cx="270" cy="270" r="85" fill="#e9e9e9"/>
    <circle cx="270" cy="270" r="62" fill="url(#hubFill)"/>
    <circle cx="270" cy="270" r="36" fill="#bdbdbd"/>
    <circle cx="270" cy="270" r="22" fill="var(--page)"/>
  </svg>

</main>
</body>
</html>
```